Flyer-Design für Open Workspace Lösung
Zielgruppe
Was machen wir? Open Workspace Lösung für Ärzte und Psychotherapeuten.
Zielgruppe: Unser Angebot richtet sich an Ärzte, Psychologen, Psychotherapeuten, Heilpraktiker für Psychotherapie (HeilprG) sowie Coaches und Supervisoren mit vergleichbarem und zertifiziertem Hintergrund. Darüber hinaus stehen die Räume auch für Seminare, Workshops oder Gruppenangebote zur Verfügung.
Aufgabenstellung
1. Die Word-Skizze ist ein Entwurf, der gerne verändert werden kann.
2. Das Foto in der oberen Hälfte ist ein Platzhalter. Es ist zwar real aber wir haben leider noch kein gutes Foto der fertigen Räume. Daher sollte, falls ein Bild verwendet wird, eine bearbeitbare Version mitgeliefert werden, damit wir das Bild noch austauschen können. Es muss kein Bild im Flyer verwendet werden, kann aber.
3. Unser Logo sollte auf den Flyer kommen. Es gibt das Logo mit und ohne Text. Beide hängen wir als Datei mit an.
4. Wir haben eine Website: www.praxis-sonnenquell.de
Der Flyer sollte zu dieser passen. Die Schriftart der Website ist font-famliy: 'Lato', sans-serif und sollte verwendet werden.
5. Die Farbe (türkis) ist vorgegeben. Die Definition ist: #0CE0AE
Die Grautöne der Website sind folgende: #444444, #555444, #5A5A5A, #888888, #CCCCCC #F4F4F4
6. wir hätten gerne einen one-pager, den man als Werbung an Emails anhängen und im Internet veröffentlichen kann und einen Flyer, der ausgedruckt ausliegen kann

```html
<!DOCTYPE html>
<html lang="de">
<head>
<meta charset="utf-8">
<title>Praxis am Sonnenquell – Flyer</title>
<link href="https://fonts.googleapis.com/css2?family=Lato:ital,wght@0,300;0,400;0,700;1,300;1,400;1,700;1,900&display=swap" rel="stylesheet">
<style>
:root{
  --teal:#5dbd9d;
  --teal-mid:#8fd1ba;
  --teal-light:#b9e3d3;
  --teal-pale:#eaf5f0;
  --frame:#d8ece4;
  --box-grey:#f1f3f2;
  --ink:#444444;
  --ink-soft:#5a5a5a;
  --heading-dark:#24594a;
  --page:#ffffff;
  --bg:#ececec;
}
*{box-sizing:border-box;margin:0;padding:0}
html,body{width:776px;height:1200px;overflow:hidden}
body{background:var(--bg);font-family:'Lato',sans-serif;color:var(--ink);position:relative}
.spread{position:absolute;left:28px;width:720px;height:566px;display:flex;background:var(--frame);padding:7px;box-shadow:0 6px 16px rgba(0,0,0,.12)}
.spread--outside{top:18px}
.spread--inside{top:616px}
.panel{position:relative;width:50%;height:100%;background:var(--page);overflow:hidden}
.panel + .panel{margin-left:7px}

/* back panel */
.back{padding:18px 14px 14px}
.back__intro{font-style:italic;font-size:12.5px;line-height:1.45;padding:0 8px;color:var(--ink)}
.back__intro b{font-weight:900}
.contacts{background:var(--teal-pale);margin:12px 0 0;padding:10px 8px}
.contact + .contact{margin-top:10px}
.contact__name{font-style:italic;font-weight:900;color:var(--teal);font-size:12.5px;margin-bottom:3px}
.contact__line{font-style:italic;font-size:10px;line-height:1.55}
.back__rule{height:1.5px;background:var(--teal);margin:16px 10px 18px}
.back__brand{padding:0 10px;font-weight:700;font-size:16px;line-height:1.2;color:var(--ink);display:flex;align-items:center;gap:8px}
.back__brand .mark{width:12px;height:12px;background:var(--teal);flex:none}
.back__address{padding:0 10px;margin-top:10px;font-size:10.5px;line-height:1.45}
.map{position:relative;margin:10px 10px 0;height:142px;background:linear-gradient(135deg,#f1f1f1,#e2e2e2 55%,#ececec)}
.map svg{position:absolute;left:50%;top:42%;transform:translate(-50%,-50%)}

/* cover */
.cover__brand{position:absolute;left:18px;top:40px;font-weight:700;font-size:26px;line-height:1.15;color:var(--teal)}
.cover__photo{position:absolute;left:0;top:150px;width:100%;height:420px;background:linear-gradient(180deg,#fbfbfa 0%,#f2f2ef 45%,#e7e6e2 100%)}
.cover__title{position:absolute;left:18px;top:140px;font-style:italic;font-weight:700;font-size:18.5px;line-height:1.2;color:var(--ink)}
.cover__shapes{position:absolute;left:0;bottom:0}
.cover__address{position:absolute;right:14px;bottom:28px;text-align:right;font-style:italic;font-size:10.5px;line-height:1.5;color:#2f6f5a}

/* inside left */
.inside-left{padding:16px 12px}
.hook{font-style:italic;font-size:12.5px;line-height:1.4;color:var(--ink)}
.hook b{font-weight:700;color:var(--teal)}
.hook--left{border-left:2px solid var(--teal);padding-left:10px;margin:0 8px}
.hook--right{border-right:2px solid var(--teal);padding-right:10px;text-align:right;margin:14px 8px 0 60px}
.band{position:relative;margin:22px -12px 0;height:42px}
.band svg{position:absolute;left:0;top:0}
.band__text{position:relative;padding:6px 0 0 24px;color:#fff;font-weight:700;font-size:12.5px;line-height:1.22}
.info{background:var(--box-grey);margin:16px 6px 0;padding:9px 9px 10px}
.info h2{font-size:13px;font-weight:700;color:var(--ink);margin-bottom:5px}
.info p{font-size:9.1px;line-height:1.62;color:var(--ink)}

/* inside right */
.inside-right{padding:14px 14px 12px}
.rooms h2{font-size:13px;font-weight:700;margin-bottom:4px}
.rooms__lead{font-size:9.1px;line-height:1.5}
.rooms ul{list-style:none;margin-top:6px}
.rooms li{font-size:9.1px;line-height:1.6;padding-left:8px;position:relative;margin-bottom:5px}
.rooms li::before{content:"•";position:absolute;left:0}
.room{display:flex;height:126px;margin-top:10px}
.room:first-of-type{margin-top:6px}
.room__photo{width:46%;background:linear-gradient(160deg,#f4f3f0,#dcdad5 70%,#c9c7c1)}
.room__info{width:54%;background:var(--teal);color:#fff;padding:8px 10px}
.room__info h3{font-size:13.5px;font-weight:700;color:var(--heading-dark);margin-bottom:3px}
.room__features{font-style:italic;font-weight:300;font-size:9.3px;line-height:1.35;color:#eefaf5}
.room__price{font-style:normal;font-weight:700;font-size:12.5px;margin-top:6px;color:#fff}
.room__price sup{font-size:7px}
.rooms__footer{font-size:9.1px;line-height:1.5;margin-top:10px}
.rooms__footer b{font-weight:700}
</style>
</head>
<body>

<section class="spread spread--outside">
  <article class="panel back">
    <p class="back__intro"><b>Bei Fragen</b>, für weitere Informationen oder zur <b>Vereinbarung einer Besichtigung</b> - gerne auch virtuell über Video - kontaktieren Sie uns:</p>
    <div class="contacts">
      <div class="contact">
        <p class="contact__name">Carla Weidner-Holm</p>
        <p class="contact__line">Email: kontakt@praxis-sonnenquell.de</p>
        <p class="contact__line">Tel.: 0176 48152907</p>
      </div>
      <div class="contact">
        <p class="contact__name">Jonas Holm</p>
        <p class="contact__line">Email: kontakt@praxis-sonnenquell.de</p>
        <p class="contact__line">Tel.: 0177 3906625</p>
      </div>
    </div>
    <div class="back__rule"></div>
    <div class="back__brand"><span class="mark"></span><span>Praxis am Sonnenquell</span></div>
    <p class="back__address">Lindenhofstraße 9<br>80337 München<br>kontakt@praxis-sonnenquell.de<br>www.praxis-sonnenquell.de</p>
    <div class="map" role="img" aria-label="Stadtplan-Ausschnitt mit dem Standort der Praxis">
      <svg width="12" height="17" viewBox="0 0 12 17" aria-hidden="true"><path d="M6 0C2.7 0 0 2.6 0 5.9 0 10 6 17 6 17s6-7 6-11.1C12 2.6 9.3 0 6 0z" fill="#2f80c8"/><circle cx="6" cy="6" r="2.2" fill="#fff"/></svg>
    </div>
  </article>

  <article class="panel cover">
    <div class="cover__photo" role="img" aria-label="Heller Praxisraum mit zwei grauen Sesseln, kleinem Tisch mit Blumen und großer Fensterfront"></div>
    <p class="cover__brand">Praxis am Sonnenquell</p>
    <h1 class="cover__title">Flexible Raummiete<br>im Herzen von München</h1>
    <svg class="cover__shapes" width="353" height="230" viewBox="0 0 353 230" aria-hidden="true">
      <polygon points="0,60 353,0 353,230 0,230" fill="var(--teal-light)" opacity=".75"/>
      <polygon points="0,60 353,115 353,230 0,230" fill="var(--teal-mid)"/>
      <polygon points="0,150 353,30 353,230 0,230" fill="var(--teal)" opacity=".9"/>
    </svg>
    <p class="cover__address">Lindenhofstraße 9<br>80337 München<br>kontakt@praxis-sonnenquell.de</p>
  </article>
</section>

<section class="spread spread--inside">
  <article class="panel inside-left">
    <p class="hook hook--left">Sie suchen schöne und <b>hochwertig ausgestattete Räume</b> in zentraler Lage für Therapie, Coaching oder Seminare?</p>
    <p class="hook hook--right">Sie möchten <b>zeitlich flexibel</b> arbeiten und Ihre monatlichen <b>Fixkosten niedrig</b> halten?</p>
    <div class="band">
      <svg width="330" height="42" viewBox="0 0 330 42" aria-hidden="true">
        <polygon points="0,0 330,0 310,42 0,42" fill="var(--teal-light)"/>
        <polygon points="0,0 318,0 300,38 0,38" fill="var(--teal)"/>
      </svg>
      <p class="band__text">Unsere Praxis am Sonnenquell<br>bietet Ihnen genau das.</p>
    </div>
    <div class="info">
      <h2>Die Praxis</h2>
      <p>Die Praxis liegt direkt am Sendlinger Tor, ist sehr ruhig und bietet einen wunderschönen Blick ins Grüne. In ihr stehen fünf frisch renovierte und hochwertig ausgestattete Therapieräume sowie zwei Seminarräume zur Verfügung. An welchem Tag, zu welcher Uhrzeit und für wie viele Stunden Sie diese mieten, können Sie entscheiden, ganz so wie es Ihr Bedarf von Woche zu Woche oder auch für das ganze Jahr verlangt.</p>
    </div>
    <div class="info">
      <h2>An wen richtet sich unser Angebot?</h2>
      <p>Unser Angebot richtet sich an Ärzte, Psychologen, Psychotherapeuten, Heilpraktiker für Psychotherapie (HeilprG) sowie Coaches und Supervisoren mit vergleichbarem und zertifiziertem Hintergrund. Darüber hinaus stehen die Räume auch für Seminare, Workshops oder Gruppenangebote zur Verfügung.</p>
    </div>
  </article>

  <article class="panel inside-right rooms">
    <h2>Die Räume</h2>
    <p class="rooms__lead">Verschiedene Preismodelle bieten Ihnen<br>je nach Bedarf volle Flexibilität:</p>
    <ul>
      <li>Sie können Räume entweder für einzelne Stunden oder im Abonnement mieten.</li>
      <li>Bei der Miete von einzelnen Stunden fallen keinerlei laufende Kosten an.</li>
      <li>Über ein Abonnement bieten wir Ihnen sehr attraktive Preise ab einer Stunde pro Woche.</li>
      <li>Sie können dadurch selbst bestimmen ob und in welcher Höhe Ihnen monatliche Fixkosten entstehen und welches Modell für Sie am besten geeignet ist.</li>
    </ul>
    <div class="room">
      <div class="room__photo" role="img" aria-label="Therapieraum mit Sessel, Teppich und hellen Fenstern"></div>
      <div class="room__info">
        <h3>Therapieraum</h3>
        <p class="room__features">Bequeme Sessel,<br>höhenverstellbarer<br>Schreibtisch,<br>Schreibtischstuhl,<br>Luftfilter, großzügige<br>Fensterfront</p>
        <p class="room__price">ab 17,<sup>00</sup> €/h</p>
      </div>
    </div>
    <div class="room">
      <div class="room__info">
        <h3>Seminarraum</h3>
        <p class="room__features">Flipchart, hochwertige<br>Bestuhlung,<br>Beamer<br>Hepa 13 Luftfilter,<br>großzügige<br>Fensterfront</p>
        <p class="room__price">ab 17,<sup>00</sup> €/h</p>
      </div>
      <div class="room__photo" role="img" aria-label="Seminarraum mit Stuhlreihen und großer Fensterfront"></div>
    </div>
    <p class="rooms__footer">Die genauen Konditionen, Bilder und alle weiteren Informationen finden Sie auf unserer Website<br><b>www.praxis-sonnenquell.de</b></p>
  </article>
</section>

</body>
</html>
```